Agriculture Business Card

I want to use my existing logo and use my tagline of "Don't Guess...Soil Test" on the card. Looking for a double sided card that will really get peoples attention.
Contact Info:
Marlow Field Crop Edge
Calvin Brusk
2917 K Lane
Larkin, NE 68593
402-555-0193
calvin.r.brusk@fieldmailbox.net

```html
<!DOCTYPE html>
<html lang="en">
<head>
<meta charset="utf-8">
<title>Marlow Field Crop Edge – Business Card</title>
<link href="https://fonts.googleapis.com/css2?family=Montserrat:wght@400;600&display=swap" rel="stylesheet">
<style>
  :root {
    --bg: #d6d6d6;
    --paper: #f3f2ef;
    --edge-green: #2fb52a;
    --name-green: #2eb34a;
    --brand-brown: #9b5a3c;
    --accent-gold: #fbb416;
    --text-grey: #6b6b6b;
    --emboss: #dedcd7;
  }
  * { box-sizing: border-box; margin: 0; padding: 0; }
  html, body {
    width: 1200px; height: 1051px; overflow: hidden;
    background: var(--bg);
    font-family: "Montserrat", Arial, sans-serif;
  }
  .sheet {
    width: 1200px; height: 1051px;
    display: flex; flex-direction: column; align-items: center; justify-content: center;
    gap: 60px;
  }
  .card {
    position: relative;
    width: 640px; height: 366px;
    background: var(--paper);
    border-bottom: 6px solid var(--edge-green);
    box-shadow: 0 12px 30px rgba(0,0,0,0.18);
  }
  .brand {
    display: flex; align-items: center; gap: 14px;
    color: var(--brand-brown);
    font-weight: 600;
    line-height: 1.1;
  }
  .brand-dot {
    flex: none; border-radius: 50%;
    background: var(--accent-gold);
  }
  /* Contact side */
  .card-front .brand {
    position: absolute; left: 36px; top: 110px; width: 240px;
    font-size: 24px;
  }
  .card-front .brand-dot { width: 34px; height: 34px; }
  .divider {
    position: absolute; left: 300px; top: 64px; width: 2px; height: 176px;
    background: var(--emboss);
    box-shadow: 1px 0 0 #fff;
  }
  .contact {
    position: absolute; left: 334px; top: 76px;
    color: var(--text-grey);
    font-size: 15px; line-height: 1.55;
  }
  .contact-name {
    color: var(--name-green);
    font-weight: 600; font-size: 22px; letter-spacing: 0.5px;
    text-transform: uppercase;
    margin-bottom: 14px;
  }
  .contact-address { margin-bottom: 12px; }
  .contact-line { display: flex; align-items: center; gap: 8px; }
  .contact-line svg { width: 14px; height: 14px; flex: none; fill: var(--accent-gold); }
  .tagline {
    position: absolute; left: 0; right: 0; bottom: 36px;
    text-align: center;
    color: var(--text-grey);
    font-size: 17px; letter-spacing: 1px;
  }
  /* Logo side */
  .card-back { display: flex; align-items: center; justify-content: center; }
  .card-back .brand { font-size: 34px; max-width: 380px; }
  .card-back .brand-dot { width: 48px; height: 48px; }
</style>
</head>
<body>
<main class="sheet">
  <section class="card card-front" aria-label="Card front">
    <div class="brand"><span class="brand-dot"></span><span>Marlow Field Crop Edge</span></div>
    <div class="divider"></div>
    <div class="contact">
      <p class="contact-name">Calvin Brusk</p>
      <p class="contact-address">2917 K Lane<br>Larkin, NE 68593</p>
      <p class="contact-line">
        <svg viewBox="0 0 24 24" aria-hidden="true"><path d="M6.6 10.8a15.1 15.1 0 0 0 6.6 6.6l2.2-2.2a1 1 0 0 1 1-.25 11.4 11.4 0 0 0 3.6.57 1 1 0 0 1 1 1V20a1 1 0 0 1-1 1A17 17 0 0 1 3 4a1 1 0 0 1 1-1h3.5a1 1 0 0 1 1 1c0 1.25.2 2.45.57 3.57a1 1 0 0 1-.25 1z"/></svg>
        402-555-0193
      </p>
      <p class="contact-line">
        <svg viewBox="0 0 24 24" aria-hidden="true"><path d="M2 5h20v14H2z M2 5l10 8 10-8" fill="var(--accent-gold)"/><path d="M3 6l9 7 9-7" fill="none" stroke="#fff" stroke-width="1.6"/></svg>
        calvin.r.brusk@fieldmailbox.net
      </p>
    </div>
    <p class="tagline">Don't Guess...Soil Test</p>
  </section>

  <section class="card card-back" aria-label="Card back">
    <div class="brand"><span class="brand-dot"></span><span>Marlow Field Crop Edge</span></div>
  </section>
</main>
</body>
</html>
```